Commercial Real Estate for Lease Listing Flyer

I am looking to put together a flyer for our available office space in our building. It needs to look professional and it will be standard sized 8.5 x 11 and double sided. Full color as well. This flyer will need to be able to be put in a PDF and a picture file that can be embedded in an email. I have included pictures, logo, and a Word document with the information you should need. Also, I included a bunch of SAMPLE leasing flyers that you can get ideas from. The floor plan is also included in here. I want it specifically noted that the top suite is Suite 100 and the bottom suite is 120. And list their size as well. I will be reviewing all designs very quickly, so be sure to check the comments.

• Please refer to these links for additional photos:
• "Twilight 1.jpg" at: https://files.plinthdocs.net/a/preview/3f7d1a92-b4e0-4c1a-8e5f-71c0d2ab9e34
• Twilight 2_straightened.jpg" at: https://files.plinthdocs.net/a/preview/a15c8e03-7d2b-4f9e-b6a1-0c93e4f72d58
• "Twilight 3.jpg" at: https://files.plinthdocs.net/a/preview/6e2b9f71-c3a4-4d08-9e7b-5f1a8c03d6e2
• "Twilight 4.jpg" at: https://files.plinthdocs.net/a/preview/c84a0d6e-1f3b-4e57-a2c9-9b7e05f4d813
• "Twilight 5.jpg" at: https://files.plinthdocs.net/a/preview/7b0f5c28-e6d1-4a93-8f4e-d25a1b6c07f9
• "Twilight 6.jpg" at: https://files.plinthdocs.net/a/preview/e3c6a417-5b92-4f0d-bc8e-4a1f97d2e065
• "Twilight 7.jpg" at: https://files.plinthdocs.net/a/preview/5a9d2e80-c7f4-4b16-93a0-e8b6f1c4d27a
• "Twilight 8.jpg" at: https://files.plinthdocs.net/a/preview/b2e7f069-84c3-4d5a-a71e-3c0d9b58f6e4
• "Twilight 9.jpg" at: https://files.plinthdocs.net/a/preview/4d8c1b3f-a0e5-4f72-8b69-f17e2c05a9d3
• "Twilight 10.jpg" at: https://files.plinthdocs.net/a/preview/f09a6c52-3e18-4b7d-9c24-6b5d80e1f3a7
• "Twilight 11.jpg" at: https://files.plinthdocs.net/a/preview/8e4f2d06-b9c7-4a31-85e0-d7a3c16f4b92

```html
<!DOCTYPE html>
<html lang="en">
<head>
<meta charset="utf-8">
<title>Harbor Road Centre – Leasing Flyer</title>
<link href="https://fonts.googleapis.com/css2?family=Montserrat:wght@400;500;600;800&display=swap" rel="stylesheet">
<style>
  :root{
    --brand-blue:#0f5aa0;
    --brand-blue-deep:#0b4f92;
    --paper:#ffffff;
    --ink-grey:#5e5e5e;
    --rule-tan:#b59c7c;
    --photo-warm:#c9a46c;
    --photo-wood:#6b3324;
  }
  *{box-sizing:border-box;margin:0;padding:0}
  html,body{width:946px;height:1200px;overflow:hidden;background:var(--paper)}
  body{font-family:"Montserrat",sans-serif}
  .flyer{position:relative;width:946px;height:1200px;background:var(--paper);overflow:hidden}
  .block{position:absolute;background:var(--brand-blue)}
  .spine-top{left:103px;top:0;width:310px;height:60px}
  .corner-block{left:713px;top:0;width:233px;height:228px}
  .hero-photo{position:absolute;left:44px;top:41px;width:859px;height:560px;
    background:linear-gradient(180deg,#e7dcc8 0%,var(--photo-warm) 38%,#9a7a52 62%,var(--photo-wood) 78%,#2c2522 100%)}
  .brand-box{position:absolute;left:103px;top:78px;width:310px;height:149px;background:var(--paper);
    display:flex;align-items:center;justify-content:center}
  .brand-name{color:var(--brand-blue-deep);font-weight:600;font-size:27px;letter-spacing:2px;text-transform:uppercase}
  .headline-panel{position:absolute;left:103px;top:227px;width:310px;height:374px;background:rgba(15,90,160,.86)}
  .headline{position:absolute;left:28px;top:44px;color:#fff;font-weight:800;font-size:46px;line-height:62px;letter-spacing:.5px}
  .headline-rule{position:absolute;left:26px;top:242px;width:256px;height:2px;background:var(--rule-tan)}
  .property-name{position:absolute;left:28px;top:262px;color:#fff;font-weight:600;font-size:20px;letter-spacing:.5px}
  .spec-column{left:103px;top:601px;width:310px;height:229px}
  .specs{position:absolute;left:103px;top:645px;width:843px;list-style:none}
  .spec{display:flex;align-items:center;height:29.2px}
  .spec-label{width:287px;text-align:right;color:#fff;font-size:21px;font-weight:500}
  .spec-dash{width:12px;height:3px;background:#fff;margin-left:11px}
  .spec-value{margin-left:21px;color:var(--ink-grey);font-size:16.5px;letter-spacing:.3px}
  .thumb-link{left:268px;top:826px;width:39px;height:210px}
  .thumb{position:absolute;top:836px;height:191px;
    background:linear-gradient(180deg,#d9c39b 0%,#bfa274 50%,#4a2a20 80%,#8c7f72 100%)}
  .thumb-1{left:48px;width:218px}
  .thumb-2{left:314px;width:211px}
  .thumb-3{left:580px;width:212px}
  .contact-box{left:103px;top:1036px;width:310px;height:126px;color:#fff;text-align:right;padding:10px 37px 0 0}
  .contact-title{font-weight:600;font-size:25px;line-height:37px;text-transform:uppercase}
  .contact-sub{font-size:19px;font-weight:500;line-height:24px}
  .contact-list{position:absolute;left:444px;top:1062px;list-style:none}
  .contact-item{display:flex;align-items:center;height:28px;color:var(--ink-grey);font-size:15px;letter-spacing:.2px}
  .contact-item svg{width:18px;height:18px;margin-right:20px;fill:var(--brand-blue)}
  .footer-band{left:0;top:1162px;width:946px;height:38px}
</style>
</head>
<body>
<main class="flyer">
  <div class="block spine-top"></div>
  <div class="block corner-block"></div>

  <div class="hero-photo" role="img" aria-label="Conference room with wood table, black chairs and arched window"></div>

  <div class="brand-box"><span class="brand-name">Vela Companies</span></div>

  <section class="headline-panel">
    <h1 class="headline">FLEXIBLE<br>AND<br>FOCUSED</h1>
    <div class="headline-rule"></div>
    <p class="property-name">HARBOR ROAD CENTRE</p>
  </section>

  <div class="block spec-column"></div>
  <ul class="specs">
    <li class="spec"><span class="spec-label">Name of Building</span><span class="spec-dash"></span><span class="spec-value">Harbor Road Centre</span></li>
    <li class="spec"><span class="spec-label">Address</span><span class="spec-dash"></span><span class="spec-value">4180 Harbor Road, Lakeview Gardens, FL 33499</span></li>
    <li class="spec"><span class="spec-label">Building Size</span><span class="spec-dash"></span><span class="spec-value">18,325 SF</span></li>
    <li class="spec"><span class="spec-label">Vacant SF</span><span class="spec-dash"></span><span class="spec-value">3,791 SF</span></li>
    <li class="spec"><span class="spec-label">Occupancy</span><span class="spec-dash"></span><span class="spec-value">79%</span></li>
  </ul>

  <div class="block thumb-link"></div>
  <div class="thumb thumb-1" role="img" aria-label="Private office with desk and arched window"></div>
  <div class="thumb thumb-2" role="img" aria-label="Small office with desk and framed artwork"></div>
  <div class="thumb thumb-3" role="img" aria-label="Corner office with desk and window"></div>

  <section class="block contact-box">
    <h2 class="contact-title">For Leasing<br>Information</h2>
    <p class="contact-sub">Please Contact</p>
  </section>

  <ul class="contact-list">
    <li class="contact-item"><svg viewBox="0 0 24 24"><circle cx="12" cy="7" r="5"/><path d="M2 23c0-6 4.5-9 10-9s10 3 10 9z"/></svg>Dylan Vela at</li>
    <li class="contact-item"><svg viewBox="0 0 24 24"><path d="M6.6 10.8a15.1 15.1 0 0 0 6.6 6.6l2.2-2.2a1 1 0 0 1 1-.25 11.4 11.4 0 0 0 3.6.57 1 1 0 0 1 1 1V20a1 1 0 0 1-1 1A17 17 0 0 1 3 4a1 1 0 0 1 1-1h3.5a1 1 0 0 1 1 1c0 1.25.2 2.45.57 3.57a1 1 0 0 1-.25 1z"/></svg>555-014-2937</li>
    <li class="contact-item"><svg viewBox="0 0 24 24"><path d="M2 5h20v14H2z M4 7v.4l8 5.4 8-5.4V7l-8 5.2z" fill-rule="evenodd"/></svg>dylan@velacompanies.com</li>
  </ul>

  <div class="block footer-band"></div>
</main>
</body>
</html>
```